The Linen Loft Co

We need a business card design for our wardrobe company.
Please visit our website www.gentlelinenlofts.com to get an idea of who we are.

```html
<!DOCTYPE html>
<html lang="en">
<head>
<meta charset="utf-8">
<title>The Linen Loft Co – Business Card</title>
<link href="https://fonts.googleapis.com/css2?family=Lato:wght@400;700;900&display=swap" rel="stylesheet">
<style>
  :root {
    --stage: #d9d9d9;
    --card-front: #fbf7f6;
    --card-back: #1c1c1c;
    --card-back-tone: #2a2a2a;
    --ink: #141414;
    --ink-soft: #3a3a3a;
    --paper-white: #ffffff;
  }
  html, body {
    margin: 0;
    padding: 0;
    width: 1200px;
    height: 782px;
    overflow: hidden;
    background: var(--stage);
    font-family: "Lato", sans-serif;
  }
  .stage {
    position: relative;
    width: 1200px;
    height: 782px;
  }
  .card {
    position: absolute;
    top: 236px;
    width: 540px;
    height: 310px;
    box-sizing: border-box;
    box-shadow: 0 6px 18px rgba(0,0,0,0.18);
  }
  .card-front {
    left: 40px;
    background: var(--card-front);
    color: var(--ink);
    padding: 40px 0 0 150px;
  }
  .brand {
    display: flex;
    align-items: center;
    gap: 10px;
  }
  .brand-square {
    width: 14px;
    height: 14px;
    background: var(--ink);
    flex: none;
  }
  .brand-name {
    font-weight: 900;
    font-size: 19px;
    letter-spacing: 0.5px;
    text-transform: uppercase;
    white-space: nowrap;
  }
  .tagline {
    margin: 4px 0 0 24px;
    font-weight: 700;
    font-size: 14px;
  }
  .person-name {
    margin: 26px 0 0;
    font-weight: 900;
    font-size: 19px;
    text-transform: uppercase;
    letter-spacing: 0.3px;
  }
  .person-role {
    margin: 1px 0 10px;
    font-size: 14px;
    color: var(--ink-soft);
  }
  .contact-list {
    list-style: none;
    margin: 0;
    padding: 0;
    font-size: 14.5px;
    color: var(--ink-soft);
    line-height: 1.45;
  }
  .contact-list li {
    display: flex;
    align-items: center;
    gap: 7px;
  }
  .contact-icon {
    width: 11px;
    height: 11px;
    fill: var(--ink);
    flex: none;
  }
  .address {
    margin: 2px 0 0;
    font-size: 14.5px;
    line-height: 1.35;
    color: var(--ink-soft);
  }
  .card-back {
    left: 620px;
    background: linear-gradient(135deg, var(--card-back) 0%, var(--card-back-tone) 100%);
    overflow: hidden;
  }
  .back-pattern {
    position: absolute;
    inset: 0;
    background: linear-gradient(160deg, var(--card-back-tone) 0%, var(--card-back) 60%, var(--card-back-tone) 100%);
  }
  .back-brand {
    position: absolute;
    left: 50%;
    top: 50%;
    transform: translate(-50%, -50%);
    display: flex;
    align-items: center;
    gap: 10px;
    color: var(--paper-white);
  }
  .back-brand .brand-square {
    background: var(--paper-white);
  }
</style>
</head>
<body>
<main class="stage">
  <section class="card card-front" aria-label="Business card front">
    <div class="brand">
      <span class="brand-square"></span>
      <span class="brand-name">The Linen Loft Co</span>
    </div>
    <p class="tagline">Made to Fit Every Room</p>

    <p class="person-name">Daniel Hartley</p>
    <p class="person-role">Managing Director</p>

    <ul class="contact-list">
      <li>
        <svg class="contact-icon" viewBox="0 0 12 12" aria-hidden="true"><path d="M1 2.5C1 1.7 1.7 1 2.5 1h7C10.3 1 11 1.7 11 2.5v1H8.5V2.5h-5v1H1zM2.5 5h7l1.5 5.5H1z"/></svg>
        0207 555 0148
      </li>
      <li>
        <svg class="contact-icon" viewBox="0 0 12 12" aria-hidden="true"><path d="M0.5 2h11v8h-11z M1.5 3l4.5 3.5L10.5 3" fill="var(--ink)" stroke="var(--card-front)" stroke-width="1"/></svg>
        info@gentlelinenlofts.com
      </li>
      <li>
        <svg class="contact-icon" viewBox="0 0 12 12" aria-hidden="true"><circle cx="6" cy="6" r="5.5"/><path d="M0.5 6h11M6 0.5c2 2 2 9 0 11M6 0.5c-2 2-2 9 0 11" fill="none" stroke="var(--card-front)" stroke-width="0.8"/></svg>
        www.gentlelinenlofts.com
      </li>
    </ul>
    <p class="address">Arden House, 42 Mill Lane<br>London N1 4RT</p>
  </section>

  <section class="card card-back" aria-label="Business card back">
    <div class="back-pattern" role="img" aria-label="Faint repeated brand-mark pattern in dark grey"></div>
    <div class="back-brand">
      <span class="brand-square"></span>
      <span class="brand-name">The Linen Loft Co</span>
    </div>
  </section>
</main>
</body>
</html>
```